New Business Card Design Project

We require a business card design for Vexalund, a newly established Indian company.
Our focus is on the development, manufacturing, and export of a diverse array of pharmaceutical products on a global scale. The card should convey a professional appearance, as our primary markets are in Africa, China, and Southeast Asian nations.
We envision a two-sided business card, with the reverse side dedicated to a logo set against a solid color or an elegantly designed pattern. The corners should be rounded. We would appreciate seeing both horizontal and vertical design options. We trust the designer to utilize their expertise in creating this design.

The content for the business card is included in the attached Word file.

Target Market(s)

Our primary markets are in Africa, China, and Southeast Asian, Latin America, Maldives, Sri Lanka

Industry/Entity Type

Pharmaceutical Manufacturing and Export

Contact Information for Business Card

Colors

Designer to choose colors to be used in the design.

Requirements
Must have
• The reverse side of the business card features solely the logo along with the tagline, "Care Across Borders."
Should not have
• The logo should not exceed two instances, encompassing both the front and back sides of the card.

```html
<!DOCTYPE html>
<html lang="en">
<head>
<meta charset="UTF-8">
<title>Vexalund Business Card</title>
<link href="https://fonts.googleapis.com/css2?family=Montserrat:wght@400;500;700&display=swap" rel="stylesheet">
<style>
  :root {
    --bg: #e9ecef;
    --brand-blue: #29a3db;
    --brand-blue-deep: #1d86bf;
    --brand-red: #e2533e;
    --paper: #f7f7f7;
    --white: #ffffff;
  }
  * { box-sizing: border-box; margin: 0; padding: 0; }
  html, body { width: 1200px; height: 900px; overflow: hidden; }
  body {
    background: var(--bg);
    font-family: 'Montserrat', sans-serif;
    display: flex;
    align-items: center;
    justify-content: center;
    gap: 40px;
  }
  .card {
    position: relative;
    width: 540px;
    height: 310px;
    border-radius: 22px;
    overflow: hidden;
    box-shadow: 0 10px 28px rgba(0,0,0,0.18);
  }

  /* Back side */
  .card-back { background: var(--brand-blue-deep); }
  .back-pattern {
    position: absolute; inset: 0;
    background: linear-gradient(135deg, #3aa7dc 0%, #2393cc 45%, #1a7fb6 100%);
  }
  .back-divider {
    position: absolute; left: 0; right: 0; top: 168px;
    height: 1px; background: rgba(255,255,255,0.18);
  }
  .back-brand {
    position: absolute; right: 48px; top: 78px;
    display: flex; align-items: center; gap: 8px;
  }
  .back-brand .dot {
    width: 12px; height: 12px; border-radius: 50%;
    background: var(--brand-red);
  }
  .back-brand .name {
    color: var(--white); font-weight: 700; font-size: 24px;
  }
  .tagline {
    position: absolute; left: 0; right: 0; top: 200px;
    text-align: center; color: var(--white);
    font-weight: 700; font-size: 15px; letter-spacing: 0.3px;
  }

  /* Front side */
  .card-front { background: var(--brand-blue); }
  .front-shape { position: absolute; inset: 0; }
  .front-brand {
    position: absolute; left: 340px; top: 112px; width: 190px;
    display: flex; align-items: center; justify-content: center; gap: 8px;
  }
  .front-brand .dot {
    width: 14px; height: 14px; border-radius: 50%;
    background: var(--brand-red);
  }
  .front-brand .name {
    color: var(--brand-blue); font-weight: 700; font-size: 29px;
  }
  .holder { position: absolute; left: 34px; top: 78px; color: var(--white); }
  .holder-name { font-weight: 700; font-size: 19px; }
  .holder-role { font-weight: 400; font-size: 11px; margin-top: 4px; margin-left: 16px; }
  .address {
    position: absolute; left: 66px; top: 178px;
    color: var(--white); font-size: 11px; line-height: 1.45;
  }
  .contacts {
    position: absolute; left: 44px; top: 228px;
    list-style: none; color: var(--white); font-size: 11px;
  }
  .contacts li { display: flex; align-items: center; gap: 10px; height: 20px; }
  .contacts svg { width: 12px; height: 12px; fill: var(--white); }
</style>
</head>
<body>

  <section class="card card-back" aria-label="Card back">
    <div class="back-pattern" role="img" aria-label="Repeating capsule brand pattern in tones of blue"></div>
    <div class="back-divider"></div>
    <div class="back-brand">
      <span class="dot"></span>
      <span class="name">Vexalund</span>
    </div>
    <p class="tagline">Care Across Borders</p>
  </section>

  <section class="card card-front" aria-label="Card front">
    <svg class="front-shape" viewBox="0 0 540 310" width="540" height="310">
      <path d="M352 0 H540 V262 C450 262 330 248 316 140 C310 80 326 30 352 0 Z" fill="var(--paper)"/>
      <path d="M338 28 C320 70 318 120 328 160 C348 232 420 256 500 258" fill="none" stroke="var(--brand-red)" stroke-width="3" stroke-linecap="round"/>
    </svg>

    <div class="front-brand">
      <span class="dot"></span>
      <span class="name">Vexalund</span>
    </div>

    <div class="holder">
      <p class="holder-name">Arjun K. Malvade</p>
      <p class="holder-role">CEO</p>
    </div>

    <p class="address">12, Suryakant Nagar,<br>Nashik, 422005, India</p>

    <ul class="contacts">
      <li>
        <svg viewBox="0 0 24 24"><path d="M6.6 10.8a15.1 15.1 0 0 0 6.6 6.6l2.2-2.2c.3-.3.7-.4 1-.2 1.1.4 2.3.6 3.6.6.6 0 1 .4 1 1V20c0 .6-.4 1-1 1A17 17 0 0 1 3 4c0-.6.4-1 1-1h3.5c.6 0 1 .4 1 1 0 1.3.2 2.5.6 3.6.1.3 0 .7-.2 1z"/></svg>
        <span>+919876501234</span>
      </li>
      <li>
        <svg viewBox="0 0 24 24"><path d="M2 5h20v14H2z M2 5l10 8 10-8" stroke="#29a3db" stroke-width="1.5"/></svg>
        <span>arjun@vexalund.com</span>
      </li>
      <li>
        <svg viewBox="0 0 24 24"><circle cx="12" cy="12" r="10"/><path d="M2 12h20M12 2c3 3 3 17 0 20M12 2c-3 3-3 17 0 20" stroke="#29a3db" stroke-width="1.5" fill="none"/></svg>
        <span>www.vexalund.com</span>
      </li>
    </ul>
  </section>

</body>
</html>
```